Audio Visual company needs WordPress Site re-design

We need a new, simple and sleek redesign of our website, www.kelvarosupply.net. It is crucial that it is mobile platform friendly! The company emphasis is on commercial sound and video installation.

Examples of what our company does can be found here: http://bramwickav.org/

I am NOT looking for a storefront or an e-commerce site. I would just like an elegant site that describes our services. Perhaps incorporate a sleek showcase into the homepage of projects we have completed. Also would like an elegant menu-bar, perhaps enhance our current site menu or similar.

Here is a link to another site that exhibits the content I am looking for. Their target market is also much like mine.
http://www.pollanderhouse.com/ ........ A polished up version of this site would probably be my ideal site. It has almost EXACTLY the content I am looking for. Exclude the "Printing & signage" category. Needs nicer menus, contact page and project showcase.

Here is another example: http://www.clearhavenmedia.com/ ......... This site has a very nice homepage design with a good layout and feature slider. The site is simple, elegant and to the point.

Target Market(s)

Corporate/commercial business, Educational institutions

Industry/Entity Type

E-Commerce

Font styles to use
Serif
Sans Serif

Requirements
Must have
• Mobile friendly navigation
Nice to have
• HTML5 & CSS3
Should not have
• No Adobe Flash content. No store templates or e-commerce. We are a service based company not a product sales company

```html
<!DOCTYPE html>
<html lang="en">
<head>
<meta charset="utf-8">
<title>Kelvaro Supply – Sound &amp; Video Solutions</title>
<link href="https://fonts.googleapis.com/css2?family=Roboto:wght@300;400;500;700&display=swap" rel="stylesheet">
<style>
:root{
  --navy:#0b1f66;--navy-deep:#061450;--red:#c8101a;--red-dark:#9e0a12;
  --ink:#1d2a6b;--text:#555;--light:#f2f2f2;--foot:#0d1320;--foot-deep:#080c16;
  --foot-text:#8a93a6;--star:#f29a12;
}
*{box-sizing:border-box;margin:0;padding:0}
html,body{width:748px;height:1200px;overflow:hidden}
body{position:relative;background:#f4f4f4;font-family:'Roboto',sans-serif;color:var(--text)}
.abs{position:absolute}
.header{left:0;top:0;width:748px;height:66px;background:#fff}
.brand{left:70px;top:19px;display:flex;align-items:center;gap:7px}
.brand-mark{width:16px;height:16px;background:var(--red)}
.brand-name{font-size:23px;font-weight:700;color:var(--navy);letter-spacing:.3px}
.estimate{right:70px;top:29px;text-align:right;font-size:8px;color:var(--navy)}
.estimate b{display:block;font-size:10px;font-weight:400;color:var(--red);margin-top:2px}
.nav{left:0;top:66px;width:748px;height:34px;background:linear-gradient(#1b3a9a,#0a226e 60%,#071a58)}
.nav a{position:absolute;top:0;height:34px;line-height:34px;font-size:8px;color:#fff;text-decoration:none}
.nav .active{background:var(--red);width:64px;text-align:center}
.slider{left:70px;top:112px;width:608px;height:234px;background:#fff;border:1px solid #ddd}
.slide-img{left:3px;top:3px;width:602px;height:227px;
  background:
   linear-gradient(to right,rgba(40,20,10,.35),rgba(0,0,0,0) 20%,rgba(0,0,0,0) 80%,rgba(120,20,20,.35)),
   linear-gradient(#3e2216 0%,#6e3e26 18%,#5a3322 30%,#7fa08e 36%,#b9c9a6 44%,#6c8a70 52%,#8a5538 60%,#9a6442 72%,#6a4430 84%,#3a2418 100%)}
.caption{left:23px;top:165px;width:271px;height:38px;background:rgba(235,235,235,.82);color:var(--red);font-size:12px;line-height:38px;padding-left:16px}
.dots{left:328px;top:336px;width:92px;height:16px;background:#e8e8e8;display:flex;justify-content:center;align-items:center;gap:5px}
.dots i{width:5px;height:5px;border-radius:50%;border:1px solid #aaa}
.dots i:first-child{background:var(--navy);border-color:var(--navy)}
.welcome{left:70px;top:370px;width:608px;text-align:center}
.welcome h1{font-size:13px;font-weight:400;color:var(--ink);margin-bottom:6px}
.welcome p{font-size:7px;line-height:16px;color:#444}
.btn-red{display:inline-block;background:linear-gradient(var(--red),var(--red-dark));color:#fff;font-size:7.5px;text-align:center}
.more{left:330px;top:447px;width:88px;height:29px;line-height:29px}
.service{top:490px;width:192px;text-align:center}
.service h2{font-size:9.5px;font-weight:400;color:var(--ink);margin-bottom:5px}
.service .frame{height:106px;background:#fff;border:1px solid #ddd;padding:2px}
.service .frame div{width:100%;height:100%}
.service p{font-size:6.8px;line-height:15px;margin-top:7px}
.gallery{left:0;top:678px;width:748px;height:134px;background:var(--navy-deep)}
.gallery h3{position:absolute;left:70px;top:17px;font-size:9.5px;font-weight:400;color:#fff}
.gallery .thumb{position:absolute;top:42px;height:68px;border:2px solid #fff}
.reviews{left:0;top:812px;width:748px;height:214px;background:var(--light)}
.reviews h2{position:absolute;top:25px;width:748px;text-align:center;font-size:12.5px;font-weight:400;color:var(--ink)}
.review{position:absolute;top:56px;width:140px;text-align:center}
.avatar{width:60px;height:60px;border-radius:50%;margin:0 auto;border:2px solid #ddd;background:linear-gradient(#fafafa 0%,#f0f0f0 50%,#9a9aa2 68%,#24242c 80%,#1a1a20 100%)}
.review h4{font-size:9.5px;font-weight:400;color:var(--red);margin-top:12px}
.review p{font-size:6.6px;line-height:13px;color:#888;margin-top:4px}
.stars{color:var(--star);font-size:9px;letter-spacing:1px;margin-top:1px}
.footer{left:0;top:1026px;width:748px;height:138px;background:var(--foot);color:var(--foot-text)}
.footer h5{position:absolute;top:20px;font-size:9.5px;font-weight:400;color:#fff}
.news{position:absolute;left:70px;display:flex;gap:4px}
.news .pic{width:46px;height:32px;border:1px solid #333}
.news b{display:block;font-size:7px;font-weight:400;color:#fff}
.news span{display:block;font-size:6.5px;line-height:11px;margin-top:3px}
.links a{position:absolute;font-size:6.5px;color:var(--foot-text);text-decoration:none}
.social a{position:absolute;left:429px;font-size:6.5px;color:var(--foot-text);text-decoration:none;display:flex;align-items:center;gap:5px}
.social i{width:8px;height:8px;background:#3a5a9e;display:inline-block}
.field{position:absolute;left:538px;width:140px;height:23px;background:#c5d6f0;font-size:6.5px;color:#6a7590;line-height:23px;padding-left:10px}
.sub{position:absolute;left:538px;top:96px;width:140px;height:23px;line-height:23px}
.bottom{left:0;top:1164px;width:748px;height:36px;background:var(--foot-deep);text-align:center;font-size:6.5px;line-height:36px;color:#3c4558}
</style>
</head>
<body>
<header class="abs header">
  <div class="abs brand"><span class="brand-mark"></span><span class="brand-name">Kelvaro Supply</span></div>
  <div class="abs estimate">CALL US FOR A FREE ESTIMATE<b>(555) 014-2286</b></div>
</header>
<nav class="abs nav">
  <a class="active" style="left:70px">HOME</a>
  <a style="left:162px">SERVICES</a>
  <a style="left:246px">GALLERY</a>
  <a style="left:328px">CONTACT US</a>
  <a style="left:423px">CUSTOMER REVIEWS</a>
</nav>
<section class="abs slider">
  <div class="abs slide-img" role="img" aria-label="Restaurant counter with a row of digital menu board displays above a brick wall"></div>
  <div class="abs caption">MULTI-DISPLAY DIGITAL MENU BOARDS</div>
</section>
<div class="abs dots"><i></i><i></i><i></i><i></i><i></i></div>
<section class="abs welcome">
  <h1>WELCOME TO KELVARO SUPPLY</h1>
  <p>Kelvaro Supply has been customizing audio and video products for home and business customers since 2007. We specialize in the design and installation of residential &amp;<br>commercial sound systems, HD video displays, digital projection &amp; digital signage. We are located in Ashgrove Park, a northwest suburb just outside of Brennford. Need an estimate?<br>We will come to you! All of our estimates are done at your home or office for free.</p>
</section>
<a class="abs btn-red more">READ MORE</a>
<section class="abs service" style="left:70px"><h2>AUDIO</h2><div class="frame"><div role="img" aria-label="Auditorium stage with a white projection screen between navy curtains" style="background:linear-gradient(to right,rgba(20,28,70,.9) 0%,rgba(20,28,70,0) 14%,rgba(20,28,70,0) 84%,rgba(20,28,70,.9) 100%),linear-gradient(#1c2550 0%,#c8ccd0 18%,#eceae4 45%,#d6d2c8 68%,#b8a88e 82%,#8a7a66 100%)"></div></div><p>Ut wisi enim ad minim veniam, quis nostrud exerci tation<br>ullamcorper suscipit lobortis nisl ut aliquip ex ea<br>commodo consequat.</p></section>
<section class="abs service" style="left:278px"><h2>VIDEO</h2><div class="frame"><div role="img" aria-label="Hall with projected video on the stage screen" style="background:radial-gradient(ellipse 22% 26% at 50% 62%,#c8d8f0 0%,#6a88b8 60%,rgba(0,0,0,0) 100%),linear-gradient(#8a8440 0%,#6b6630 35%,#3a3418 70%,#2a2010 100%)"></div></div><p>Ut wisi enim ad minim veniam, quis nostrud exerci tation<br>ullamcorper suscipit lobortis nisl ut aliquip ex ea<br>commodo consequat.</p></section>
<section class="abs service" style="left:486px"><h2>INSTALLATION</h2><div class="frame"><div role="img" aria-label="Ceiling-mounted projector installation" style="background:radial-gradient(ellipse 45% 40% at 45% 65%,#f4f4f4 0%,#cfcfcf 60%,rgba(0,0,0,0) 100%),linear-gradient(#e8e8e8,#8f8f8f 45%,#b9b9b9 75%,#d6d6d6)"></div></div><p>Ut wisi enim ad minim veniam, quis nostrud exerci tation<br>ullamcorper suscipit lobortis nisl ut aliquip ex ea<br>commodo consequat.</p></section>
<section class="abs gallery">
  <h3>OUR GALLERY</h3>
  <svg class="abs" style="left:651px;top:14px" width="30" height="14" viewBox="0 0 30 14"><circle cx="7" cy="7" r="6" fill="#8a93a6"/><path d="M8.5 4 5.5 7l3 3" stroke="#061450" stroke-width="1.5" fill="none"/><circle cx="21" cy="7" r="6" fill="#fff"/><path d="M19.5 4l3 3-3 3" stroke="#061450" stroke-width="1.5" fill="none"/></svg>
  <div class="thumb" style="left:70px;width:110px;background:radial-gradient(ellipse 22% 28% at 50% 45%,#c8d8f0,#5a6aa0 60%,rgba(0,0,0,0)),linear-gradient(#7a7440,#3a3418 65%,#2a1a10)" role="img" aria-label="Auditorium projection"></div>
  <div class="thumb" style="left:194px;width:110px;background:linear-gradient(#e6e6e6 0%,#d0d0d0 18%,#1c55c8 20%,#2a7ae8 50%,#0a2a80 80%,#d8d8d8 82%)" role="img" aria-label="Dual wall-mounted displays"></div>
  <div class="thumb" style="left:318px;width:110px;background:radial-gradient(ellipse 40% 35% at 45% 60%,#3a3a3a,rgba(0,0,0,0)),linear-gradient(#e2e2e2,#a8a8a8 55%,#6a6a6a)" role="img" aria-label="Projector ceiling mount"></div>
  <div class="thumb" style="left:442px;width:110px;background:radial-gradient(ellipse 35% 40% at 50% 50%,#e8c020,#3a8a2a 60%,rgba(0,0,0,0)),linear-gradient(135deg,#1a3a14,#4aa030 50%,#1a2a10)" role="img" aria-label="Display showing promotional graphic"></div>
  <div class="thumb" style="left:566px;width:112px;background:radial-gradient(ellipse 30% 40% at 62% 45%,#6a6a6a,rgba(0,0,0,0)),linear-gradient(to right,#e8e8e8 0%,#cfcfcf 12%,#1a1a1a 16%,#0a0a0a 100%)" role="img" aria-label="Equipment rack cabinet"></div>
</section>
<section class="abs reviews">
  <h2>CUSTOMER REVIEWS</h2>
  <svg class="abs" style="left:51px;top:90px" width="10" height="16"><path d="M8 2 2 8l6 6" stroke="#555" stroke-width="1.5" fill="none"/></svg>
  <svg class="abs" style="left:684px;top:90px" width="10" height="16"><path d="M2 2l6 6-6 6" stroke="#555" stroke-width="1.5" fill="none"/></svg>
  <div class="review" style="left:73px"><div class="avatar" role="img" aria-label="Customer portrait photo"></div><h4>OWEN HALE</h4><p>Lorem ipsum dolor sit amet, consectetuer adipiscing elit, sed diam nonummy nibh euismod tincidunt.</p><div class="stars">★★★★☆</div></div>
  <div class="review" style="left:225px"><div class="avatar" role="img" aria-label="Customer portrait photo"></div><h4>MARCUS REED</h4><p>Lorem ipsum dolor sit amet, consectetuer adipiscing elit, sed diam nonummy nibh euismod tincidunt.</p><div class="stars">★★★★☆</div></div>
  <div class="review" style="left:381px"><div class="avatar" role="img" aria-label="Customer portrait photo"></div><h4>PETER LANG</h4><p>Lorem ipsum dolor sit amet, consectetuer adipiscing elit, sed diam nonummy nibh euismod tincidunt.</p><div class="stars">★★★★☆</div></div>
  <div class="review" style="left:538px"><div class="avatar" role="img" aria-label="Customer portrait photo" style="background:linear-gradient(#fafafa 0%,#f0f0f0 50%,#b08a70 66%,#3a2a24 82%,#2a1e1a 100%)"></div><h4>CLARA VOSS</h4><p>Lorem ipsum dolor sit amet, consectetuer adipiscing elit, sed diam nonummy nibh euismod tincidunt.</p><div class="stars">★★★★★</div></div>
</section>
<footer class="abs footer">
  <h5 style="left:70px">LATEST NEWS</h5>
  <div class="news" style="top:40px"><div class="pic" role="img" aria-label="Project thumbnail" style="background:radial-gradient(ellipse 25% 30% at 50% 45%,#c8d8f0,#5a6aa0 60%,rgba(0,0,0,0)),linear-gradient(#7a7440,#3a3418 65%,#2a1a10)"></div><div><b>Lorem ipsum dolor sit</b><span>Ut wisi enim ad minim<br>veniam, quis nostrud...</span></div></div>
  <div class="news" style="top:88px"><div class="pic" role="img" aria-label="Project thumbnail" style="background:linear-gradient(#2a2a2a 0%,#1c55c8 25%,#2a7ae8 55%,#0a2a80 80%,#2a2a2a 100%)"></div><div><b>Lorem ipsum dolor sit</b><span>Ut wisi enim ad minim<br>veniam, quis nostrud...</span></div></div>
  <h5 style="left:249px">QUICK LINKS</h5>
  <div class="links">
    <a style="left:250px;top:38px">Home</a><a style="left:250px;top:54px">About Us</a><a style="left:250px;top:70px">Our Service</a><a style="left:250px;top:86px">FAQ</a><a style="left:250px;top:102px">Contact Us</a>
    <a style="left:319px;top:38px">Testimonials</a><a style="left:319px;top:54px">Privacy Policy</a><a style="left:319px;top:70px">Sitemap</a><a style="left:319px;top:86px">Terms &amp; Conditions</a>
  </div>
  <h5 style="left:429px">CONNECT US</h5>
  <div class="social">
    <a style="top:38px"><i></i>Friends Page</a><a style="top:54px"><i style="background:#3a8ad0"></i>Updates</a><a style="top:70px"><i style="background:#2a6ab0"></i>Network</a><a style="top:86px"><i style="background:#c8402a"></i>Circles</a><a style="top:102px"><i style="background:#e07a1a"></i>RSS</a>
  </div>
  <h5 style="left:538px">NEWSLETTER</h5>
  <div class="field" style="top:36px">Name</div>
  <div class="field" style="top:65px">Email Address</div>
  <a class="btn-red sub">SUBSCRIBE</a>
</footer>
<div class="abs bottom">Copyrights @ 2015 Kelvaro Supply. All Right Reserved.</div>
</body>
</html>
```